DeskHarbor | A Happiness Company

We need to Develop a Sales Brochure for a coworking space:
1. About DeskHarbor
2. Location
3. Cards to Show Benefits
4. Floor Plan and Pictures
5. Pricing Card

Jersey City Coworking/Shared Office Space, Steps from Millbrook LINK
Impress your clients. Stimulate your creativity. Unleash your inner genius.
DeskHarbor is Jersey City’s newest premier coworking and shared office space,

home to:

 Entrepreneurs
 Visionaries
 Freelancers
 Consultants
 Telecommuters
 Startups
 + More

Here you’ll have access to everything you need in order to work efficiently, productively, happily and healthily. Essentials, Amenities and Resources
 Furnished office space with 24/7 access
 Conference rooms and meeting spaces
 Networking events and educational workshops
 Business support
 Ultra-High Speed Internet
 Secure WiFi
 Print + Copy + Scan
 Mail service and business address
 White boards and office supplies
 Gourmet teas and coffees
 Kitchen stocked with healthy snacks
 + More

Member Discounts
 Hotel
 Travel
 Car Rental
 Cloud and server
 + More

Our Values

Collaboration, Community, Happiness, Wellness, Growth
Bonus: Our short-term funding program offers financial support to help your business reach its next milestone.
Location and Pricing
DeskHarbor is located at 248 Garden Crest Lane in Jersey City, a prestigious
address on the banks of the Hudson River, just minutes from the Barrow Causeway and steps from the Millbrook LINK station.
1. The cover of the brochure should create excitement to open the folder. Do not create a trifold. We are a very high end office space not a medical office. The size of the paper, does not have to be standard. Think card stock, matt or Glossy or Both

2. On Opening the Brochure - The First Page is to educate my client with a art, color and words
3. Page 2,3,4 and 5Is about Inspiration and explanation: I am thinking that they should be cards of detail:
1. Orange: Vision - Consider a theme of Innovation, High Performance, Fun, Value from action, resources, impulse
2. Gold: Details: Orange: Vision - Consider a theme of Authority and Leadership. The duty to Shine, the leader being the backbone of the group. Practial, values of home, status, security, and traditions
3. Blue: Encourage and support, A peacemaker, Think about themes of caring, counseling, nurturing, Idealistic and sympathetic. This is about contribution
4. Green: The Independent thinker, seeking knowledge, intelligence, justice and insight. About the details

The message on these cards should be similar but at various levels of detail

The 5th Card is about Floor Plans - You are not responsible for it this card. Just the Look of how the card should look like

The 6th Card is about pricing
Updates

Reason: Only 1 designer has provided a decent design. Most of the submissions were recycled and not in line. Please extend by 4 weeks.

Target Market(s)

- Technology Companies (10 people or less)
- Entrepreneurs (2 People)
- Freelancers (1 People)
- small size Technology Company (5 people or less)

Industry/Entity Type

It Company

Font styles to use
Other font styles liked:
• Caviar Dreams and Sans Serif

Requirements
Must have
• - Pictures
• - Details
• - Inspiration
• - FLoor plans
• - Questions and Value
• - Minimal
• Why would they want to buy your product? 
• What's the most important thing it can do for them?
• What is the most important problem your product or service can solve for them?
• To be effective, your brochure needs to get attention, get the prospect interested enough to read further, raise their desire for the product or service, and get them to take a specific action such as buy now, call and make an appointment, return a post card.
Nice to have
• I am open to design - be inspirational
• Should be clear
• They are interested in themselves and/or their own businesses. To get their attention, your brochure needs to focus on the benefits they will enjoy by making a purchase from you.
Should not have
• Cannot be too Salesy
• No Stock pictures
• Don't put a picture of your building on the cover of the brochure
• The only thing they care about is whether or not your products meet their needs.

```html
<!DOCTYPE html>
<html lang="en">
<head>
<meta charset="utf-8">
<title>DeskHarbor Brochure — Floor Plans &amp; Price</title>
<link href="https://fonts.googleapis.com/css2?family=Source+Sans+3:wght@300;400;700&display=swap" rel="stylesheet">
<style>
  :root {
    --backdrop: #c4c4c4;
    --slate: #737373;
    --paper: #ffffff;
    --ink: #1e1e1e;
    --muted: #8c8c8c;
    --on-slate: #f2f2f2;
    --orange: #f06a35;
    --gold: #f2b934;
    --blue: #3f93d6;
    --green: #7fb23a;
    --accent-green: #9cc63c;
    --accent-blue: #4fb6ea;
  }
  * { box-sizing: border-box; margin: 0; padding: 0; }
  html, body { width: 1200px; height: 1168px; overflow: hidden; }
  body {
    background: var(--backdrop);
    font-family: "Source Sans 3", sans-serif;
    font-weight: 300;
    position: relative;
  }
  .spread {
    position: absolute;
    left: 117px;
    width: 961px;
    height: 481px;
    box-shadow: 2px 3px 6px rgba(0,0,0,.25);
    overflow: hidden;
  }
  .spread--plans { top: 70px; background: var(--slate); color: var(--on-slate); }
  .spread--price { top: 585px; background: var(--paper); }

  .spread--plans::after {
    content: ""; position: absolute; left: 470px; top: 0; width: 20px; height: 100%;
    background: linear-gradient(90deg, rgba(0,0,0,0), rgba(0,0,0,.05) 50%, rgba(0,0,0,0));
  }
  .spread--price::after {
    content: ""; position: absolute; left: 420px; top: 0; width: 61px; height: 100%;
    background: linear-gradient(90deg, rgba(0,0,0,0), rgba(0,0,0,.07));
  }

  .page-title {
    position: absolute; font-weight: 300; font-size: 28px; line-height: 1; letter-spacing: .2px;
  }
  .spread--plans .page-title { left: 39px; top: 38px; }
  .spread--price .page-title { left: 54px; top: 73px; color: var(--ink); }

  .line { display: block; white-space: nowrap; }

  .page-intro {
    position: absolute; left: 39px; top: 79px;
    font-size: 11px; line-height: 14.4px;
  }

  .plan { position: absolute; top: 138px; width: 188px; height: 186px; }
  .plan-drawing {
    width: 100%; height: 100%;
    background: radial-gradient(circle, rgba(255,255,255,.16), rgba(255,255,255,0) 70%);
    clip-path: polygon(50% 0, 100% 50%, 50% 100%, 0 50%);
  }
  .plan-badge {
    position: absolute; top: 359px; width: 36px; height: 36px; margin-left: -18px;
    border-radius: 50%; color: #fff; font-weight: 700; font-size: 27px;
    display: flex; align-items: center; justify-content: center; line-height: 1;
  }
  .plan-caption {
    position: absolute; top: 407px; width: 170px; margin-left: -85px;
    text-align: center; font-size: 11px; line-height: 14.4px;
  }

  .price-block {
    position: absolute;
    font-size: 11.4px; line-height: 14.4px; color: var(--muted);
  }
  .price-block p + p { margin-top: 14.4px; }

  .accent-field {
    position: absolute; left: 0; top: 230px; width: 180px; height: 251px;
    background:
      radial-gradient(ellipse at 30% 70%, rgba(79,182,234,.35), rgba(79,182,234,0) 65%),
      radial-gradient(ellipse at 20% 30%, rgba(156,198,60,.35), rgba(156,198,60,0) 65%);
  }
</style>
</head>
<body>

<section class="spread spread--plans">
  <h1 class="page-title">Floor Plans</h1>
  <p class="page-intro"><span class="line">Collaboration, Community,</span><span class="line">Happiness, Wellness, Growth</span></p>

  <div class="plan" style="left:40px"><div class="plan-drawing" role="img" aria-label="Floor plan 1, white line drawing"></div></div>
  <div class="plan" style="left:254px"><div class="plan-drawing" role="img" aria-label="Floor plan 2, white line drawing"></div></div>
  <div class="plan" style="left:520px"><div class="plan-drawing" role="img" aria-label="Floor plan 3, white line drawing"></div></div>
  <div class="plan" style="left:733px"><div class="plan-drawing" role="img" aria-label="Floor plan 4, white line drawing"></div></div>

  <span class="plan-badge" style="left:132px;background:var(--orange)">1</span>
  <span class="plan-badge" style="left:342px;background:var(--gold)">2</span>
  <span class="plan-badge" style="left:614px;background:var(--blue)">3</span>
  <span class="plan-badge" style="left:827px;background:var(--green)">4</span>

  <p class="plan-caption" style="left:129px"><span class="line">Collaboration, Community,</span><span class="line">Happiness, Wellness, Growth</span></p>
  <p class="plan-caption" style="left:339px"><span class="line">Collaboration, Community,</span><span class="line">Happiness, Wellness, Growth</span></p>
  <p class="plan-caption" style="left:615px"><span class="line">Collaboration, Community,</span><span class="line">Happiness, Wellness, Growth</span></p>
  <p class="plan-caption" style="left:825px"><span class="line">Collaboration, Community,</span><span class="line">Happiness, Wellness, Growth</span></p>
</section>

<section class="spread spread--price">
  <div class="accent-field" role="img" aria-label="Decorative green and blue accent"></div>

  <h2 class="page-title">Price</h2>

  <div class="price-block" style="left:321px;top:83px">
    <p><span class="line">Collaboration, Communi-</span><span class="line">ty, Happiness, Wellness,</span><span class="line">Growth</span></p>
    <p><span class="line">Bonus: Our short-term</span><span class="line">funding program offers</span><span class="line">financial support to help</span><span class="line">your business reach its</span><span class="line">next milestone.</span></p>
  </div>
  <div class="price-block" style="left:509px;top:83px">
    <p><span class="line">Collaboration, Community,</span><span class="line">Happiness, Wellness,</span><span class="line">Growth</span></p>
    <p><span class="line">Bonus: Our short-term</span><span class="line">funding program offers</span><span class="line">financial support to help</span><span class="line">your business reach its next</span><span class="line">milestone.</span></p>
  </div>
  <div class="price-block" style="left:654px;top:83px">
    <p><span class="line">Collaboration, Community,</span><span class="line">Happiness, Wellness,</span><span class="line">Growth</span></p>
    <p><span class="line">Bonus: Our short-term</span><span class="line">funding program offers</span><span class="line">financial support to help</span><span class="line">your business reach its next</span><span class="line">milestone.</span></p>
  </div>
  <div class="price-block" style="left:799px;top:83px">
    <p><span class="line">Collaboration, Community,</span><span class="line">Happiness, Wellness,</span><span class="line">Growth</span></p>
    <p><span class="line">Bonus: Our short-term</span><span class="line">funding program offers</span><span class="line">financial support to help</span><span class="line">your business reach its next</span><span class="line">milestone.</span></p>
  </div>

  <div class="price-block" style="left:318px;top:307px">
    <p><span class="line">Collaboration, Community,</span><span class="line">Happiness, Wellness,</span><span class="line">Growth</span></p>
    <p><span class="line">Bonus: Our short-term</span><span class="line">funding program offers</span><span class="line">financial support to help</span><span class="line">your business reach its next</span><span class="line">milestone.</span></p>
  </div>
  <div class="price-block" style="left:509px;top:307px">
    <p><span class="line">Collaboration, Community,</span><span class="line">Happiness, Wellness,</span><span class="line">Growth</span></p>
    <p><span class="line">Bonus: Our short-term</span><span class="line">funding program offers</span><span class="line">financial support to help</span><span class="line">your business reach its next</span><span class="line">milestone.</span></p>
  </div>
  <div class="price-block" style="left:654px;top:307px">
    <p><span class="line">Collaboration, Community,</span><span class="line">Happiness, Wellness,</span><span class="line">Growth</span></p>
    <p><span class="line">Bonus: Our short-term</span><span class="line">funding program offers</span><span class="line">financial support to help</span><span class="line">your business reach its next</span><span class="line">milestone.</span></p>
  </div>
  <div class="price-block" style="left:799px;top:307px">
    <p><span class="line">Collaboration, Community,</span><span class="line">Happiness, Wellness,</span><span class="line">Growth</span></p>
    <p><span class="line">Bonus: Our short-term</span><span class="line">funding program offers</span><span class="line">financial support to help</span><span class="line">your business reach its next</span><span class="line">milestone.</span></p>
  </div>
</section>

</body>
</html>
```